Commercial Real Estate Property Sign

Design a 4' x 4' sign that pops. Refer to examples.

Must include the following information:
A space to list (For Sale, For Lease, Build-to-Suite or Available)
BrightKeel,LLC
Commercial Real Estate
company website
My Name (Marcus Pellow)
My Phone #

Industry/Entity Type

Real Estate

```html
<!DOCTYPE html>
<html lang="en">
<head>
<meta charset="utf-8">
<title>BrightKeel LLC – Space for Lease Sign</title>
<link href="https://fonts.googleapis.com/css2?family=Barlow:wght@400;500;700;800&display=swap" rel="stylesheet">
<style>
  :root {
    --charcoal: #3a3a3b;
    --orange: #e86608;
    --ink: #1d1d1d;
    --white: #ffffff;
  }
  html, body {
    margin: 0;
    padding: 0;
    width: 1200px;
    height: 1200px;
    overflow: hidden;
    background: var(--white);
  }
  .sign {
    position: relative;
    width: 1200px;
    height: 1200px;
    background: var(--orange);
    font-family: "Barlow", Arial, sans-serif;
    color: var(--ink);
    overflow: hidden;
  }
  .sign-header {
    position: absolute;
    inset: 0 0 auto 0;
    height: 274px;
    background: var(--charcoal);
  }
  .brand {
    position: absolute;
    top: 52px;
    left: 0;
    right: 0;
    display: flex;
    justify-content: center;
    align-items: center;
    gap: 34px;
  }
  .brand-mark {
    width: 54px;
    height: 114px;
    background: var(--ink);
  }
  .brand-name {
    font-weight: 500;
    font-size: 104px;
    line-height: 1;
    letter-spacing: 0.18em;
    color: var(--white);
    white-space: nowrap;
  }
  .tagline {
    position: absolute;
    top: 176px;
    left: 0;
    right: 0;
    display: flex;
    align-items: center;
    gap: 22px;
  }
  .tagline-rule {
    flex: 1;
    height: 3px;
    background: var(--orange);
  }
  .tagline-text {
    font-weight: 500;
    font-size: 44px;
    letter-spacing: 0.02em;
    color: var(--white);
    white-space: nowrap;
  }
  .listing-status {
    position: absolute;
    top: 445px;
    left: 0;
    right: 0;
    margin: 0;
    text-align: center;
    font-weight: 800;
    font-size: 114px;
    line-height: 1;
    color: var(--white);
    letter-spacing: 0.005em;
  }
  .listing-status .initial { color: var(--ink); }
  .agent-name {
    position: absolute;
    top: 722px;
    left: 0;
    right: 0;
    text-align: center;
    font-weight: 400;
    font-size: 94px;
    line-height: 1;
    letter-spacing: 0.02em;
  }
  .agent-phone {
    position: absolute;
    top: 850px;
    left: 0;
    right: 0;
    text-align: center;
    font-weight: 800;
    font-size: 122px;
    line-height: 1;
    letter-spacing: 0.03em;
  }
  .website {
    position: absolute;
    top: 1068px;
    left: 0;
    right: 0;
    display: flex;
    justify-content: center;
    align-items: center;
    gap: 18px;
    font-weight: 800;
    font-size: 72px;
    line-height: 1;
  }
  .website-icon { width: 56px; height: 56px; }
</style>
</head>
<body>
  <main class="sign">
    <header class="sign-header">
      <div class="brand">
        <span class="brand-mark" aria-hidden="true"></span>
        <span class="brand-name">BrightKeel LLC</span>
      </div>
      <div class="tagline">
        <span class="tagline-rule"></span>
        <span class="tagline-text">Commercial Real Estate</span>
        <span class="tagline-rule"></span>
      </div>
    </header>

    <h1 class="listing-status"><span class="initial">F</span>or Space for <span class="initial">L</span>ease</h1>

    <div class="agent-name">Marcus Pellow</div>
    <div class="agent-phone">469.555.0172</div>

    <div class="website">
      <svg class="website-icon" viewBox="0 0 56 56" aria-hidden="true" fill="none" stroke="#1d1d1d" stroke-width="4">
        <circle cx="28" cy="28" r="24"/>
        <ellipse cx="28" cy="28" rx="10" ry="24"/>
        <line x1="4" y1="28" x2="52" y2="28"/>
        <line x1="8" y1="16" x2="48" y2="16"/>
        <line x1="8" y1="40" x2="48" y2="40"/>
      </svg>
      <span class="website-url">www.MyBrightKeel.com</span>
    </div>
  </main>
</body>
</html>
```